Innovative coffee bean bag design for roasters

We need a design which can be printed on a coffee bean bag but which could also work on a sticker of similar size. We're after quirky, geeky, playful and innovative. Something that will stand out and communicate the character of our business. It should be eye catching and draw the customer in for a closer look.
Thematically, think organic and earthy.
It needs an element which can be changed for different coffee origins and roast profiles, so the main design will remain the same but with a feature which changes to help the customer know what they're looking at and will make them smile.
Approximate dimensions we need are 15cm by 12cm, with the 15cm being the vertical height of the bag image. (The image will be viewed in portrait). This is the main print area - however, if you have a great idea for a full bag image (approximately 23cm by 13cm), feel free to submit this too, we're interested in all ideas.
There is an image attached of a white partially see-through bag which we are considering using, so keep this in mind when designing.
We will need our logo including - see attached image.
Finally, we need space for the information about the coffee, such as origin, roast profile, flavour notes - see attached image for an example of the information (not necessarily a stylistic indicator). Please suggest fonts etc.

Target Market(s)

coffee roasters

Requirements
Must have
• Must say under the logo coffee roasters( Copper Kettle Organic Coffee Roasters )
Nice to have
• Unique symbol, shapes, scientific.

```html
<!DOCTYPE html>
<html lang="en">
<head>
<meta charset="utf-8">
<title>Millbrook Coffee Roaster – Bag Label</title>
<link href="https://fonts.googleapis.com/css2?family=Rokkitt:wght@800&family=Kaushan+Script&family=Courgette&family=Arimo&family=Tinos:ital@1&display=swap" rel="stylesheet">
<style>
  :root {
    --page: #ffffff;
    --taupe: #6e6560;
    --ink: #231f20;
    --copper: #c8873f;
    --leaf: #8a7560;
    --white: #ffffff;
    --rule: #9a9390;
    --band-dark: #231f20;
    --band-mid: #5e5550;
    --band-light: #a59c97;
    --band-pale: #d3cecb;
    --band-copper: #c8873f;
  }
  * { box-sizing: border-box; margin: 0; padding: 0; }
  html, body { width: 1200px; height: 1200px; overflow: hidden; background: var(--page); }
  .canvas { position: relative; width: 1200px; height: 1200px; }

  .label {
    position: absolute; left: 290px; top: 207px;
    width: 627px; height: 781px;
    background: var(--ink); overflow: hidden;
  }
  .label__backdrop { position: absolute; inset: 0; }

  .leaf-art {
    position: absolute; top: 0; width: 210px; height: 280px;
    background: linear-gradient(160deg, rgba(200,135,63,0.35), rgba(200,135,63,0.08));
  }
  .leaf-art--left { left: 0; }
  .leaf-art--right { right: 0; }

  .brand-seal {
    position: absolute; left: 236px; top: 33px;
    width: 156px; height: 156px; border-radius: 50%;
    background: var(--white); border: 5px solid var(--copper);
    display: flex; align-items: center; justify-content: center; text-align: center;
    font-family: "Arimo", sans-serif; font-size: 16px; line-height: 1.2;
    color: var(--ink); padding: 18px;
  }

  .brand-name {
    position: absolute; left: 0; right: 0; top: 245px; text-align: center;
    font-family: "Rokkitt", serif; font-weight: 800; font-size: 64px;
    letter-spacing: 2px; color: var(--copper); line-height: 1;
  }
  .brand-sub {
    position: absolute; left: 0; right: 0; top: 302px; text-align: center;
    font-family: "Kaushan Script", cursive; font-size: 40px;
    color: var(--white); line-height: 1;
  }

  .tree-icon {
    position: absolute; left: 270px; top: 360px; width: 88px; height: 84px;
    background: linear-gradient(180deg, #8a817c, #5e5550); border-radius: 40px 40px 6px 6px;
  }

  .tasting-notes {
    position: absolute; left: 410px; top: 378px; width: 190px;
    transform: rotate(-12deg); text-align: center;
    font-family: "Courgette", cursive; font-size: 20px; line-height: 1.05;
    color: var(--copper);
  }

  .coffee-facts {
    position: absolute; left: 44px; top: 439px; width: 466px;
    border-left: 1.5px solid var(--rule);
    font-family: "Arimo", sans-serif; font-size: 20px; color: var(--white);
  }
  .coffee-facts li {
    list-style: none; height: 33px; line-height: 33px; padding-left: 34px;
    border-top: 1.5px solid var(--rule);
  }
  .coffee-facts li:nth-child(n+6) { width: 360px; }

  .net-weight {
    position: absolute; left: 413px; top: 642px; width: 178px; height: 68px;
    border: 2px solid var(--white); border-bottom: none; border-radius: 22px 22px 0 0;
    font-family: "Arimo", sans-serif; font-size: 20px; color: var(--white);
    display: flex; align-items: center; justify-content: center;
  }

  .profile-band {
    position: absolute; left: 0; right: 0; bottom: 0; height: 59px;
    display: grid; grid-template-columns: repeat(5, 1fr);
    font-family: "Tinos", serif; font-style: italic; font-size: 25px;
  }
  .profile-band span { display: flex; align-items: center; justify-content: center; }
  .profile--chocolate { background: var(--band-dark); color: var(--white); }
  .profile--fruity { background: var(--band-mid); color: var(--white); }
  .profile--sweet { background: var(--band-light); color: var(--white); }
  .profile--bright { background: var(--band-pale); color: var(--white); }
  .profile--juicy { background: var(--band-copper); color: var(--white); }
</style>
</head>
<body>
<div class="canvas">
  <section class="label">
    <svg class="label__backdrop" width="627" height="781" viewBox="0 0 627 781" aria-hidden="true">
      <rect width="627" height="316" fill="var(--taupe)"/>
      <polygon points="0,316 314,126 627,316 627,781 0,781" fill="var(--ink)"/>
    </svg>

    <div class="leaf-art leaf-art--left" role="img" aria-label="Line-drawn copper coffee leaf branch"></div>
    <div class="leaf-art leaf-art--right" role="img" aria-label="Line-drawn copper coffee leaf branch"></div>

    <div class="brand-seal">Copper Kettle Organic Coffee Roasters</div>

    <h1 class="brand-name">MILLBROOK</h1>
    <p class="brand-sub">Coffee Roaster</p>

    <div class="tree-icon" role="img" aria-label="Small grey coffee tree emblem"></div>

    <p class="tasting-notes">Tasting Notes:<br>Persimmon,<br>mango, macadamia<br>and sunflower</p>

    <ul class="coffee-facts">
      <li>Farm: Las Brisas</li>
      <li>Productor: Mateo Alvarez</li>
      <li>Location: Huila</li>
      <li>Altitude: 1900 - 2000 meters</li>
      <li>Varieties: Caturra</li>
      <li>Process: Washed</li>
      <li>Roast Date 7/23</li>
    </ul>

    <div class="net-weight">Net WT. 250 g</div>

    <div class="profile-band">
      <span class="profile--chocolate">Chocolate</span>
      <span class="profile--fruity">Fruity</span>
      <span class="profile--sweet">Sweet</span>
      <span class="profile--bright">Bright</span>
      <span class="profile--juicy">Juicy</span>
    </div>
  </section>
</div>
</body>
</html>
```